Custom Software Solutions

web design for a small custom programming company in Brisbane Australia. Specialize in business finance solutions, Office Suite automation and programming and data analysis. The design should portray professionalism and honesty. Main applications deal with financial accounting reporting and analysis. Would like to see colors blue and purple used (but sparsely). added file is company logo. Trading name is TR Solutions, while the official company name is TR Solutions (QLD) Pty Ltd.

Target Market(s)

current clients for support
marketing tool for prospective clients

Industry/Entity Type

Business

Number of Pages Required

5+ page

Font styles to use
Sans Serif

Colors
0555a3
a54599
ffffff

Requirements
Must have
• introduction
• blog for news and tips
• previous and current clients/projects page
• contact us page with email submission form
Should not have
• social media links

```html
<!DOCTYPE html>
<html lang="en">
<head>
<meta charset="utf-8">
<title>TR Solutions</title>
<link rel="stylesheet" href="https://fonts.googleapis.com/css2?family=Open+Sans:wght@400;600&family=Roboto:wght@400;500&display=swap">
<style>
:root{
  --blue:#0555a3;
  --blue-top:#1a66ad;
  --purple:#a54599;
  --purple-dark:#7c2f86;
  --white:#ffffff;
  --grey-band:#e9e9e9;
  --text:#555555;
  --text-dark:#222222;
  --footer:#0a52a0;
}
*{margin:0;padding:0;box-sizing:border-box}
html,body{width:1066px;height:1200px;overflow:hidden;background:var(--white)}
body{position:relative;font-family:"Open Sans",Arial,sans-serif;color:var(--text)}
.abs{position:absolute}

.topbar{left:0;top:0;width:1066px;height:52px;background:var(--blue-top)}
.header-band{left:0;top:52px;width:1066px;height:140px;background:var(--blue)}
.grey-band{left:0;top:192px;width:1066px;height:99px;background:var(--grey-band)}

.brand{left:160px;top:0;width:174px;height:93px;background:var(--white);display:flex;align-items:center;justify-content:center;gap:8px}
.brand-dot{width:14px;height:14px;border-radius:50%;background:var(--blue)}
.brand-name{font-size:17px;font-weight:600;color:var(--blue);letter-spacing:.5px}

.contact{top:16px;display:flex;align-items:center;gap:8px;color:var(--white);font-size:11.5px}
.contact.email{left:565px}
.contact.phone{left:776px}

.nav{top:103px;left:160px;height:35px;width:746px}
.nav a{position:absolute;top:0;height:35px;line-height:35px;color:var(--white);text-decoration:none;font-size:11.5px;font-weight:600;letter-spacing:.2px}
.nav a.active{background:linear-gradient(var(--purple),var(--purple-dark));width:84px;text-align:center;left:0}

.slider-frame{left:160px;top:146px;width:746px;height:414px;background:var(--white)}
.slider{left:174px;top:160px;width:718px;height:392px;background:linear-gradient(90deg,#2a3340 0%,#3b4a5e 30%,#6f8eb5 55%,#a9c5e4 75%,#3a4f78 100%)}
.dots{left:504px;top:522px;display:flex;gap:11px}
.dots span{width:12px;height:12px;border-radius:50%;background:rgba(160,170,185,.8)}
.dots span.on{background:var(--white)}

.feature{top:568px;width:239px;height:81px;background:var(--blue);color:var(--white);display:flex;align-items:center}
.feature svg{flex:none}
.feature h3{font-size:14px;font-weight:600;line-height:23px;text-transform:uppercase;white-space:nowrap}
.feature.finance svg{margin-left:26px}
.feature.finance h3{margin-left:17px}
.feature.office svg{margin-left:27px}
.feature.office h3{margin-left:14px}
.feature.data svg{margin-left:23px}
.feature.data h3{margin-left:11px}

.section-title{font-family:"Roboto",Arial,sans-serif;font-weight:400;font-size:19px;color:var(--blue);text-transform:uppercase}
.welcome-title{left:160px;top:668px}
.welcome-text{left:160px;top:697px;width:480px;font-size:10.2px;line-height:18.4px}
.welcome-photo{left:651px;top:680px;width:255px;height:145px;background:linear-gradient(135deg,#5b85b8,#d6e0ea 55%,#7a8593)}

.news-title{left:160px;top:853px}
.news{top:890px;width:236px}
.news .photo{width:227px;height:118px}
.news h4{margin-top:6px;font-size:10.7px;font-weight:400;line-height:17px;color:var(--text-dark)}
.news p{margin-top:4px;font-size:9.6px;line-height:14px;color:#777}
.news .meta{margin-top:8px;display:flex;justify-content:space-between;align-items:center;width:227px}
.date{background:var(--blue);color:var(--white);font-family:"Roboto",Arial,sans-serif;font-size:12px;padding:0 11px;height:28px;line-height:28px}
.more{font-family:"Roboto",Arial,sans-serif;font-size:12px;color:var(--purple);text-transform:uppercase}

.services-title{left:668px;top:853px}
.services{left:670px;top:872px;list-style:none}
.services li{display:flex;align-items:center;height:36.5px;font-size:10.7px;color:#333}
.services li svg{margin-right:9px}

.footer{left:0;top:1148px;width:1066px;height:52px;background:var(--footer);color:var(--white);font-size:10.5px}
.footer a{position:absolute;top:19px;color:var(--white);text-decoration:none}
.footer .copy{position:absolute;top:19px;right:161px}
</style>
</head>
<body>
<div class="abs topbar"></div>
<div class="abs header-band"></div>
<div class="abs grey-band"></div>

<div class="abs brand"><span class="brand-dot"></span><span class="brand-name">TR Solutions</span></div>

<div class="abs contact email">
  <svg width="20" height="18" viewBox="0 0 20 18"><rect x="1" y="5" width="18" height="12" fill="none" stroke="#fff" stroke-width="1.6"/><path d="M1 5l9 7 9-7M4 5V1h12v4" fill="none" stroke="#fff" stroke-width="1.6"/></svg>
  <span>office@tr-solutions.com</span>
</div>
<div class="abs contact phone">
  <svg width="20" height="20" viewBox="0 0 20 20"><path d="M4 6c0 6 4 11 10 12l2-3-3-2-2 1c-2-1-4-3-4-5l1-2-2-3z" fill="#fff"/><circle cx="15" cy="5" r="4" fill="#fff"/></svg>
  <span>+61-4-01234567 (intl)</span>
</div>

<nav class="abs nav">
  <a class="active" href="#">HOME</a>
  <a href="#" style="left:120px">ABOUT US</a>
  <a href="#" style="left:236px">SERVICES</a>
  <a href="#" style="left:347px">PROJECTS</a>
  <a href="#" style="left:460px">RESOURCES</a>
  <a href="#" style="left:584px">FAQ</a>
  <a href="#" style="left:669px">CONTACTS</a>
</nav>

<div class="abs slider-frame"></div>
<div class="abs slider" role="img" aria-label="Business team in suits standing in a bright office"></div>
<div class="abs dots"><span></span><span class="on"></span><span></span></div>

<div class="abs feature finance" style="left:160px">
  <svg width="36" height="34" viewBox="0 0 36 34" fill="#fff"><rect x="0" y="6" width="16" height="3"/><rect x="0" y="11" width="16" height="3"/><rect x="0" y="16" width="16" height="3"/><rect x="0" y="21" width="16" height="3"/><rect x="0" y="26" width="16" height="3"/><rect x="4" y="1" width="14" height="3"/><circle cx="26" cy="22" r="9" fill="none" stroke="#fff" stroke-width="2"/><text x="26" y="27" font-size="13" text-anchor="middle" font-family="Arial">$</text></svg>
  <h3>Business Finance<br>Solutions</h3>
</div>
<div class="abs feature office" style="left:412px">
  <svg width="38" height="36" viewBox="0 0 38 36" fill="#fff"><rect x="0" y="16" width="5" height="18"/><rect x="7" y="8" width="5" height="26"/><rect x="14" y="0" width="5" height="34"/><circle cx="24" cy="22" r="7" fill="none" stroke="#fff" stroke-width="3"/><path d="M28 27l7 7" stroke="#fff" stroke-width="4"/></svg>
  <h3>Office Suite<br>Automation</h3>
</div>
<div class="abs feature data" style="left:667px">
  <svg width="44" height="32" viewBox="0 0 44 32" fill="#fff"><rect x="0" y="0" width="20" height="5"/><rect x="23" y="0" width="21" height="5"/><rect x="0" y="9" width="9" height="5"/><rect x="12" y="9" width="20" height="5"/><rect x="35" y="9" width="9" height="5"/><rect x="0" y="18" width="20" height="5"/><rect x="23" y="18" width="21" height="5"/><rect x="0" y="27" width="9" height="5"/><rect x="12" y="27" width="20" height="5"/><rect x="35" y="27" width="9" height="5"/></svg>
  <h3>Programming and<br>Data Analysis</h3>
</div>

<h2 class="abs section-title welcome-title">Welcome!</h2>
<div class="abs welcome-text">
  <p>Masroin dictum fasme usce euismos eanda.Naslor siamet oremsum kertyade riaserades ieasceing elit jerrtas derase heriame fasntum nislaseraris accumsan nullael diam. Sed in lacus ut enimadi piscing aliquet. Nulla venenatis.</p>
  <p>In pasavenede mi, aliquet sit amet, euismod in, auctor utliquam dapibus tincidunt metus. Praesent justo dolor, lobortis quis, lobortis dignissim, pulvinar ac, lorem. Vestibulum sed ante. Donec sagittis euismod purus.Kertsdefer lerose mero ugdas orbinart eraesrto erebilores as nae dedskertsdefer lerose merro ugdas orbinart.</p>
</div>
<div class="abs welcome-photo" role="img" aria-label="Hands reviewing a document beside a laptop and coffee cup"></div>

<h2 class="abs section-title news-title">Latest News</h2>
<article class="abs news" style="left:161px">
  <div class="photo" role="img" aria-label="Newspaper, desk globe and keyboard in blue tones" style="background:linear-gradient(120deg,#9cc0e8,#5a8fd0 50%,#c8dcf0)"></div>
  <h4>Lorem ipsum dolor sit amet, consectetuer adipiscing elit, sed diam nonummy nibh</h4>
  <p>Ut wisi enim ad minim veniam, quis nostrud exerci tation ullamcorper suscipit...</p>
  <div class="meta"><span class="date">SEP 23 2014</span><span class="more">Read More</span></div>
</article>
<article class="abs news" style="left:413px">
  <div class="photo" role="img" aria-label="Team meeting around a white table with a laptop" style="background:linear-gradient(135deg,#3a3f47,#d9dde2 45%,#f2f2f2 60%,#4a4f58)"></div>
  <h4>Eodem modo typi, qui nunc nobis videntur parum clari, fiant sollemnes in futurum</h4>
  <p>Ut wisi enim ad minim veniam, quis nostrud exerci tation ullamcorper suscipit...</p>
  <div class="meta"><span class="date">SEP 23 2014</span><span class="more">Read More</span></div>
</article>

<h2 class="abs section-title services-title">Our Services</h2>
<ul class="abs services">
  <li><svg width="18" height="18" viewBox="0 0 18 18"><circle cx="9" cy="9" r="8" fill="#f1f1f1" stroke="#d0d0d0"/><path d="M7.5 5.5L11 9l-3.5 3.5" fill="none" stroke="#333" stroke-width="1.8"/></svg>Eodem modo typi, qui nunc nobis</li>
  <li><svg width="18" height="18" viewBox="0 0 18 18"><circle cx="9" cy="9" r="8" fill="#f1f1f1" stroke="#d0d0d0"/><path d="M7.5 5.5L11 9l-3.5 3.5" fill="none" stroke="#333" stroke-width="1.8"/></svg>Mirum est notare quam littera</li>
  <li><svg width="18" height="18" viewBox="0 0 18 18"><circle cx="9" cy="9" r="8" fill="#f1f1f1" stroke="#d0d0d0"/><path d="M7.5 5.5L11 9l-3.5 3.5" fill="none" stroke="#333" stroke-width="1.8"/></svg>Typi non habent claritatem insitam</li>
  <li><svg width="18" height="18" viewBox="0 0 18 18"><circle cx="9" cy="9" r="8" fill="#f1f1f1" stroke="#d0d0d0"/><path d="M7.5 5.5L11 9l-3.5 3.5" fill="none" stroke="#333" stroke-width="1.8"/></svg>Lorem ipsum dolor sit amet</li>
  <li><svg width="18" height="18" viewBox="0 0 18 18"><circle cx="9" cy="9" r="8" fill="#f1f1f1" stroke="#d0d0d0"/><path d="M7.5 5.5L11 9l-3.5 3.5" fill="none" stroke="#333" stroke-width="1.8"/></svg>Ut wisi enim ad minim veniam</li>
  <li><svg width="18" height="18" viewBox="0 0 18 18"><circle cx="9" cy="9" r="8" fill="#f1f1f1" stroke="#d0d0d0"/><path d="M7.5 5.5L11 9l-3.5 3.5" fill="none" stroke="#333" stroke-width="1.8"/></svg>Typi non habent claritatem insitam</li>
  <li><svg width="18" height="18" viewBox="0 0 18 18"><circle cx="9" cy="9" r="8" fill="#f1f1f1" stroke="#d0d0d0"/><path d="M7.5 5.5L11 9l-3.5 3.5" fill="none" stroke="#333" stroke-width="1.8"/></svg>Mirum est notare quam littera</li>
</ul>

<footer class="abs footer">
  <a href="#" style="left:161px">Home</a>
  <a href="#" style="left:212px">About Us</a>
  <a href="#" style="left:278px">Contact Us</a>
  <a href="#" style="left:351px">Privacy Policy</a>
  <a href="#" style="left:433px">Sitemap</a>
  <span class="copy">Copyright ©2014 tr-solutions. All Right Reserved.</span>
</footer>
</body>
</html>
```